Home decoration company - sustainable wall panels

- I would need you to design 5-10 pages for my client's website.
- The design should have details of wall panels that are being sold on the website - movelterra.com.
- It should have wood + sustainability branding.
- please focus on using shapes of products that are being sold on the website and use them as design for branding

See more here
https://sheets.quorvix.net/d/7kpRtW2nLqZ8bYhMfGcVdXsJ4eTuA9wN3oHiKy5BzPl/edit?usp=sharing

Target Market(s)

people who are want sustainable home/business wall decor

Industry/Entity Type

Interior Decoration

Logo Text

Movel Terra (for favicon, "MT")

Number of Pages Required

5+ page

Font styles to use
Serif
Sans Serif

Requirements
Must have
• - details of products that are being sold on the website movelterra.com (you will see there are different wall panel shapes)
- great creative design ideas
- follow instructions from here https://sheets.quorvix.net/d/7kpRtW2nLqZ8bYhMfGcVdXsJ4eTuA9wN3oHiKy5BzPl/edit?usp=sharing
- the design must be at least 2 levels above the current one on movelterra.com
- use photos from here https://files.quorvix.net/folders/5tWmQeRb8YuNc2XkLpAsDv3ZhGj7FiO-?usp=sharing
Nice to have
• - it would be nice if you would give your own creative suggestions
Should not have
• - should not look like it's a 1990s website

```html
<!DOCTYPE html>
<html lang="en">
<head>
<meta charset="utf-8">
<title>Door – Movel Terra</title>
<link href="https://fonts.googleapis.com/css2?family=Oswald:wght@500;600;700&family=Poppins:wght@400;500;600;700&display=swap" rel="stylesheet">
<style>
:root{
  --brown-dark:#3a1a06;
  --brown:#6e310c;
  --brown-btn:#7b3a0e;
  --accent:#c8741c;
  --star:#f2a11c;
  --text:#3c3c3c;
  --muted:#777;
  --white:#fff;
  --footer-bg:#ededed;
  --field:#e2e2e2;
}
*{margin:0;padding:0;box-sizing:border-box}
html,body{width:1200px;height:4105px;overflow:hidden}
body{position:relative;background:var(--white);font-family:'Poppins',sans-serif;color:var(--text)}
.abs{position:absolute}
.head{font-family:'Oswald',sans-serif;font-weight:600;color:var(--brown-dark);text-transform:uppercase;letter-spacing:-1px;white-space:nowrap}

/* top bar */
.topbar{left:0;top:0;width:1200px;height:29px;background:var(--brown-dark);color:var(--white);font-size:11px;display:flex;align-items:center;justify-content:space-between;padding:0 88px}
.topbar .contact{display:flex;gap:26px}
.topbar .contact span::before{content:"";display:inline-block;width:6px;height:6px;border-radius:50%;background:var(--accent);margin-right:7px;vertical-align:middle}

/* nav */
.nav{left:0;top:29px;width:1200px;height:70px;background:var(--white)}
.brand{left:88px;top:3px;width:94px;height:64px;border:2px solid var(--brown-dark);display:flex;align-items:center;justify-content:center;font-size:13px;font-weight:600;color:var(--brown-dark);text-align:center;line-height:1.1}
.menu{right:88px;top:0;height:70px;display:flex;align-items:center;gap:28px;font-family:'Oswald',sans-serif;font-weight:500;font-size:12.5px;color:var(--brown-dark);text-transform:uppercase}
.menu .active{color:var(--accent)}

/* hero */
.hero{left:0;top:99px;width:1200px;height:215px;background:linear-gradient(180deg,#6d5a4a,#4a3a2c 60%,#5a4634)}
.hero-title{left:0;top:176px;width:1200px;text-align:center;font-family:'Oswald',sans-serif;font-weight:600;font-size:36px;color:var(--white);letter-spacing:-1px}
.hero-sub{left:0;top:226px;width:1200px;text-align:center;font-weight:600;font-size:19px;color:var(--white)}

/* intro */
.section-title{left:0;width:1200px;text-align:center;font-size:33px}
.intro{left:200px;top:466px;width:800px;text-align:center;font-size:13.5px;line-height:21px;color:#555}

/* process band */
.band{left:86px;top:829px;width:1022px;height:459px;background:var(--brown-dark)}
.band-photo{top:669px;width:303px;height:346px}
.dots{position:absolute;bottom:26px;left:0;width:100%;display:flex;justify-content:center;gap:4px}
.dots i{width:7px;height:7px;border-radius:50%;background:rgba(255,255,255,.55)}
.dots i.on{background:var(--white)}
.step-title{top:1040px;font-family:'Oswald',sans-serif;font-weight:600;font-size:30px;color:var(--white);text-transform:uppercase;letter-spacing:-1px}
.step-text{top:1084px;width:285px;font-size:12.5px;line-height:19.5px;color:var(--white)}
.step-text p+p{margin-top:10px}

/* products */
.product-title{left:88px;font-size:36px;letter-spacing:-1.2px}
.rating{left:88px;font-weight:600;font-size:17px;color:var(--brown-dark);letter-spacing:.5px}
.rating b{color:var(--star)}
.specs{left:88px;width:520px;font-size:13.5px;line-height:21px;color:#555}
.specs p{margin-bottom:10px}
.price{left:88px;font-family:'Oswald',sans-serif;font-weight:600;font-size:27px;color:var(--brown)}
.btn{background:var(--brown-btn);color:var(--white);font-weight:700;font-size:18px;display:flex;align-items:center;justify-content:center;text-transform:uppercase}
.shop{left:88px;width:157px;height:44px}
.review{left:413px;width:331px;height:201px;background:var(--white);box-shadow:0 8px 30px rgba(0,0,0,.12);padding:42px 36px 0}
.review p{font-size:13.5px;line-height:21px;color:#444}
.review .stars{color:var(--star);font-size:13px;letter-spacing:3px;margin-top:2px}
.review .name{font-weight:600;color:var(--brown);font-size:15px;margin-top:-2px}
.review .arrows{position:absolute;right:30px;bottom:40px;display:flex;gap:18px}
.main-photo{left:646px;width:465px;height:499px}
.thumb{width:112px;height:111px}

.load{left:497px;top:3480px;width:204px;height:56px;background:var(--brown-dark);font-size:19px}

/* footer */
.footer{left:0;top:3612px;width:1200px;height:493px;background:radial-gradient(circle at 10% 20%,#f4f4f4,#e9e9e9 60%,#efefef)}
.foot-brand{left:88px;top:3727px;width:202px;height:139px;border:3px solid var(--brown-dark);background:#f6efe4;display:flex;align-items:center;justify-content:center;font-size:24px;font-weight:600;color:var(--brown-dark)}
.foot-head{top:3730px;font-size:24px}
.foot-list{top:3778px;font-size:13px;line-height:24px;color:#666;list-style:none}
.foot-contact{left:545px;top:3778px;font-size:12.5px;line-height:19px;color:#666}
.foot-contact div{display:flex;gap:8px;margin-bottom:3px}
.foot-contact svg{flex:none;margin-top:3px}
.social{left:549px;top:3847px;display:flex;gap:18px}
.social i{width:14px;height:14px;border-radius:3px;background:var(--brown-btn)}
.field{left:830px;width:243px;background:var(--field);font-size:11px;color:#666;padding:8px 14px}
.submit{left:830px;top:3945px;width:91px;height:29px;font-size:12px}
.rule{left:88px;top:4044px;width:1024px;height:1px;background:#cfcfcf}
.to-top{left:1134px;top:4029px;width:31px;height:31px;border-radius:50%;background:var(--brown-dark)}
.copy{left:0;top:4065px;width:1200px;text-align:center;font-size:15px;color:#333}
</style>
</head>
<body>

<!-- top bar -->
<div class="abs topbar">
  <span>Ordering larger quantities? Call us.</span>
  <div class="contact">
    <span>phone number : +1 555 014 2788</span>
    <span>Email : studio@movelterra.com, orders@movelterra.com</span>
  </div>
</div>

<!-- nav -->
<header class="abs nav">
  <div class="abs brand">Movel<br>Terra</div>
  <nav class="abs menu">
    <span>Home</span><span>Wall Paneling</span><span class="active">Door</span><span>Cutting Boards</span><span>Table Tops</span><span>About Us</span><span>Contact Us</span>
  </nav>
</header>

<!-- hero -->
<div class="abs hero" role="img" aria-label="Workshop floor with stacked wood and craftspeople at work, darkened"></div>
<h1 class="abs hero-title">DOOR</h1>
<p class="abs hero-sub">100% Sustainable. 100% Hand Crafted. 100% Unique.</p>

<!-- intro -->
<h2 class="abs head section-title" style="top:414px">How it's made</h2>
<p class="abs intro">We search the shores of East Java for teak fishermen's boats and barns which are no longer usable and transform them into panels.This also provides local fisherman a sustainable income. Every panel is unique given they are expertly handmade using different combinations of boat pieces and reclaimed wood.</p>

<h2 class="abs head section-title" style="top:593px">How we build our products</h2>

<div class="abs band"></div>

<div class="abs band-photo" style="left:135px;background:linear-gradient(160deg,#8fa6b0,#6d6a5a 55%,#5b4330)" role="img" aria-label="Worker reclaiming timber from an old fishing boat on the shore">
  <div class="dots"><i></i><i class="on"></i><i></i><i></i></div>
</div>
<div class="abs band-photo" style="left:451px;background:linear-gradient(160deg,#9a8874,#b49a7a 50%,#7b6450)" role="img" aria-label="Craftsman dismantling boat wood into small pieces">
  <div class="dots"><i></i><i class="on"></i><i></i><i></i></div>
</div>
<div class="abs band-photo" style="left:765px;background:linear-gradient(160deg,#6b3f22,#a8683a 50%,#4a2a16)" role="img" aria-label="Restaurant interior finished with reclaimed wood panels">
  <div class="dots"><i></i><i class="on"></i><i></i><i></i></div>
</div>

<h3 class="abs step-title" style="left:134px">Reclaim</h3>
<div class="abs step-text" style="left:134px">
  <p>We search the shores of East Java for teak-wood fishermen's boats and barns which are no longer usable andtransform them into gorgeous and durable décor for your home or business.slider</p>
  <p>Using irreparable boats and barns not only provides raw material, it also provides local fisherman a sustainableincome.</p>
</div>
<h3 class="abs step-title" style="left:451px">Recycle</h3>
<div class="abs step-text" style="left:451px;top:1086px">
  <p>Each of these unique boats or pieces is pains-takingly dismantled by master craftsmen. The wood is then dried for 8-12 months to ensure exceptional durability.</p>
</div>
<h3 class="abs step-title" style="left:768px">Create</h3>
<div class="abs step-text" style="left:768px;top:1093px">
  <p>Every panel is unique given they are expertly handmade using different combinations of boat pieces and reclaimedwood.</p>
  <p>Quality is our top priority. All our products under-go rigorous inspection before packaging.</p>
</div>

<!-- product 1 -->
<h2 class="abs head product-title" style="top:1452px">Ripple Board RP-210</h2>
<div class="abs rating" style="top:1502px">RATING: 5.00 <b>★</b></div>
<div class="abs specs" style="top:1537px">
  <p>GBRS: these boards may help qualify your project for GBRS points RC 4.1 &amp; 4.2 (Recycled Content) and AQ 4.4 (low VOC emission)</p>
  <p>TCC Certified: These products have a Chain-of-Custody TCC certification as well as the Timber Legality Verification by the Veralis authority.</p>
  <p>Plank dimensions: L 47.75 x W 11.75 x T 0.75<br>Eco-conscious manufacturing.</p>
</div>
<div class="abs price" style="top:1690px">$5.99</div>
<div class="abs btn shop" style="top:1739px">Shop now</div>
<div class="abs main-photo" style="top:1372px;background:linear-gradient(160deg,#d9dadb,#f3f3f3 45%,#bdbfc1)" role="img" aria-label="White paneled door laid flat in the workshop"></div>
<div class="abs thumb" style="left:646px;top:1883px;background:#9a7b5a" role="img" aria-label="Mixed teak strip panel"></div>
<div class="abs thumb" style="left:764px;top:1883px;background:#a88b6d" role="img" aria-label="Patchwork reclaimed wood panels"></div>
<div class="abs thumb" style="left:882px;top:1883px;background:#8a7a62" role="img" aria-label="Pyramid relief wood panel"></div>
<div class="abs thumb" style="left:1000px;top:1883px;background:#c2a27a" role="img" aria-label="Carved wooden panel detail"></div>
<div class="abs review" style="top:1651px">
  <p>Lorem Ipsum is simply dummy text of the printing and typesetting industry. Lorem Ipsum has been the industry's standard dummy text.</p>
  <div class="stars">★★★★★</div>
  <div class="name">Dana Reyes</div>
  <div class="arrows"><svg width="8" height="12"><path d="M7 1 2 6l5 5" fill="none" stroke="#222" stroke-width="2"/></svg><svg width="8" height="12"><path d="M1 1l5 5-5 5" fill="none" stroke="#222" stroke-width="2"/></svg></div>
</div>

<!-- product 2 -->
<h2 class="abs head product-title" style="top:2147px">Teak Prism Board TP-118</h2>
<div class="abs rating" style="top:2197px">RATING: 5.00 <b>★</b></div>
<div class="abs specs" style="top:2232px">
  <p>GBRS: these boards may help qualify your project for GBRS points RC 4.1 &amp; 4.2 (Recycled Content) and AQ 4.4 (low VOC emission)</p>
  <p>TCC Certified: These products have a Chain-of-Custody TCC certification as well as the Timber Legality Verification by the Veralis authority.</p>
  <p>Plank dimensions: L 47.75" x 11.75" x T 0.75"<br>Eco-conscious manufacturing.</p>
</div>
<div class="abs price" style="top:2385px">$5.99</div>
<div class="abs btn shop" style="top:2440px">Shop now</div>
<div class="abs main-photo" style="top:2067px;background:linear-gradient(160deg,#c79a62,#a9743f 50%,#d2aa75)" role="img" aria-label="Teak door with triangular relief pattern"></div>
<div class="abs thumb" style="left:646px;top:2577px;background:#7a5a40" role="img" aria-label="Long strip mosaic panel"></div>
<div class="abs thumb" style="left:764px;top:2577px;background:#c9a179" role="img" aria-label="Four-point star wood panel"></div>
<div class="abs thumb" style="left:882px;top:2577px;background:#b8a07a" role="img" aria-label="Stacked reclaimed teak planks"></div>
<div class="abs thumb" style="left:1000px;top:2577px;background:#d3c1a2" role="img" aria-label="Finished door on workshop bench"></div>
<div class="abs review" style="top:2346px">
  <p>Lorem Ipsum is simply dummy text of the printing and typesetting industry. Lorem Ipsum has been the industry's standard dummy text.</p>
  <div class="stars">★★★★★</div>
  <div class="name">Dana Reyes</div>
  <div class="arrows"><svg width="8" height="12"><path d="M7 1 2 6l5 5" fill="none" stroke="#222" stroke-width="2"/></svg><svg width="8" height="12"><path d="M1 1l5 5-5 5" fill="none" stroke="#222" stroke-width="2"/></svg></div>
</div>

<!-- product 3 -->
<h2 class="abs head product-title" style="top:2857px">Teak Block Board TB-305</h2>
<div class="abs rating" style="top:2907px">RATING: 5.00 <b>★</b></div>
<div class="abs specs" style="top:2942px">
  <p>GBRS: these boards may help qualify your project for GBRS points RC 4.1 &amp; 4.2 (Recycled Content) and AQ 4.4 (low VOC emission)</p>
  <p>TCC Certified: These products have a Chain-of-Custody TCC certification as well as the Timber Legality Verification by the Veralis authority.</p>
  <p>Plank dimensions: L 47.75" x 11.75" x T 0.75"<br>Eco-conscious manufacturing.</p>
</div>
<div class="abs price" style="top:3095px">$5.99</div>
<div class="abs btn shop" style="top:3149px">Shop now</div>
<div class="abs main-photo" style="top:2777px;background:linear-gradient(160deg,#c9c2b8,#7d705c 50%,#b7ad9c)" role="img" aria-label="Door with raised square teak block mosaic"></div>
<div class="abs thumb" style="left:646px;top:3287px;background:#8a6448" role="img" aria-label="Interior wall with wood mosaic"></div>
<div class="abs thumb" style="left:764px;top:3287px;background:#9b9690" role="img" aria-label="Panels stacked in warehouse"></div>
<div class="abs thumb" style="left:882px;top:3287px;background:#b59e84" role="img" aria-label="Panel being packed in box"></div>
<div class="abs thumb" style="left:1000px;top:3287px;background:#9c7a56" role="img" aria-label="Close view of stacked wood blocks"></div>
<div class="abs review" style="top:3056px">
  <p>Lorem Ipsum is simply dummy text of the printing and typesetting industry. Lorem Ipsum has been the industry's standard dummy text.</p>
  <div class="stars">★★★★★</div>
  <div class="name">Dana Reyes</div>
  <div class="arrows"><svg width="8" height="12"><path d="M7 1 2 6l5 5" fill="none" stroke="#222" stroke-width="2"/></svg><svg width="8" height="12"><path d="M1 1l5 5-5 5" fill="none" stroke="#222" stroke-width="2"/></svg></div>
</div>

<div class="abs btn load">Load more</div>

<!-- footer -->
<footer class="abs footer"></footer>
<div class="abs foot-brand">Movel Terra</div>

<h4 class="abs head foot-head" style="left:351px">Navigation</h4>
<ul class="abs foot-list" style="left:351px">
  <li>Home</li><li>Wall panels</li><li>Doors</li><li>Cutting boards</li><li>About us</li>
</ul>

<h4 class="abs head foot-head" style="left:542px">Contact us</h4>
<div class="abs foot-contact">
  <div><svg width="11" height="11" viewBox="0 0 24 24"><path d="M6.6 10.8a15 15 0 0 0 6.6 6.6l2.2-2.2c.3-.3.7-.4 1-.2 1.1.4 2.3.6 3.6.6.6 0 1 .4 1 1V20c0 .6-.4 1-1 1A17 17 0 0 1 3 4c0-.6.4-1 1-1h3.5c.6 0 1 .4 1 1 0 1.3.2 2.5.6 3.6.1.3 0 .7-.2 1z" fill="#7b3a0e"/></svg><span>Phone number +1 555 014 2788</span></div>
  <div><svg width="11" height="9" viewBox="0 0 24 18"><rect width="24" height="18" rx="2" fill="#7b3a0e"/><path d="M1 2l11 8 11-8" fill="none" stroke="#fff" stroke-width="2"/></svg><span>Email us : studio@movelterra.com,<br>orders@movelterra.com</span></div>
</div>
<div class="abs social"><i></i><i></i><i></i></div>

<h4 class="abs head foot-head" style="left:827px">Contact form</h4>
<div class="abs field" style="top:3768px;height:29px">Name</div>
<div class="abs field" style="top:3802px;height:28px">Email</div>
<div class="abs field" style="top:3838px;height:99px">Message</div>
<div class="abs btn submit">Submit</div>

<div class="abs rule"></div>
<div class="abs to-top"><svg width="31" height="31"><path d="M10 18l5.5-5.5L21 18" fill="none" stroke="#fff" stroke-width="2"/></svg></div>
<p class="abs copy">Copyright 2020 | All Rights Reserved</p>

</body>
</html>
```